Baby Food product, packaging design

Tot Harvest is a home-made style, frozen baby food service. The business provides frozen puree and textured baby food blends in ice-cube like freezer trays.

I am after 9 designs to be used as my front of package sticker, this will include the product name, logo, nutritional panel and other things as per the uploaded document.

***On my document I forgot to add that the second container is 9cm in width (Across) and 13cm in length (down).

```html
<!DOCTYPE html>
<html lang="en">
<head>
<meta charset="UTF-8">
<title>Tot Harvest – Sunny Medley label</title>
<link href="https://fonts.googleapis.com/css2?family=Patrick+Hand&family=Arimo:wght@400;700&display=swap" rel="stylesheet">
<style>
  :root {
    --page: #ffffff;
    --peach: #f2c28e;
    --grey-dark: #7d7d80;
    --grey-mid: #9a9a9d;
    --grey-light: #bdbdc0;
    --panel: #ececec;
    --sky: #2fbfe0;
    --cream: #f4e9c6;
    --red: #c3202f;
    --ink: #2a2a2a;
    --pill: #3aa9df;
    --step-num: #5cc9df;
  }
  * { margin: 0; padding: 0; box-sizing: border-box; }
  html, body { width: 1200px; height: 1200px; overflow: hidden; background: var(--page); }
  .label { position: absolute; left: 76px; top: 63px; width: 1051px; height: 1050px; }
  .side-instructions { position: absolute; left: 0; top: 0; width: 495px; height: 1050px; background: var(--peach); }
  .side-instructions .backdrop { position: absolute; inset: 0; }
  .brand-disc {
    position: absolute; left: 64px; top: 14px; width: 352px; height: 352px; border-radius: 50%;
    background: var(--sky); display: flex; align-items: center; justify-content: center;
  }
  .brand-name { font-family: "Patrick Hand", cursive; font-size: 50px; color: var(--cream); letter-spacing: 2px; }
  .instructions-title { position: absolute; left: 27px; top: 420px; font-family: "Patrick Hand", cursive; font-size: 58px; color: var(--ink); }
  .step { position: absolute; left: 51px; width: 460px; height: 107px; }
  .step-bar {
    position: absolute; left: 40px; top: 0; right: 0; bottom: 0;
    background: linear-gradient(180deg, var(--grey-mid), var(--grey-dark));
    border-radius: 0 6px 6px 0;
  }
  .step-number {
    position: absolute; left: 0; top: -6px; width: 120px; height: 120px; border-radius: 50%;
    background: radial-gradient(circle, var(--step-num) 0 46px, #e6e6e6 47px 52px, var(--grey-light) 53px);
    display: flex; align-items: center; justify-content: center;
    font-family: "Patrick Hand", cursive; font-size: 50px; color: #fff;
  }
  .step-text { position: absolute; left: 135px; top: 8px; font-family: "Patrick Hand", cursive; font-size: 30px; line-height: 46px; color: #fff; }
  .step-1 { top: 520px; } .step-2 { top: 684px; } .step-3 { top: 841px; }

  .side-product { position: absolute; left: 495px; top: 0; width: 556px; height: 1050px; background: var(--panel); font-family: "Arimo", Arial, sans-serif; }
  .product-name {
    position: absolute; left: 49px; top: 41px; width: 435px; height: 125px; border-radius: 24px;
    background: var(--red); color: #fff; font-weight: 700; font-size: 50px;
    display: flex; align-items: center; justify-content: center;
  }
  .ingredients { position: absolute; left: 0; width: 556px; top: 185px; text-align: center; color: var(--red); font-weight: 700; font-size: 31px; line-height: 38px; }
  .nutrition-title { position: absolute; left: 138px; top: 284px; color: var(--red); font-weight: 700; font-size: 20px; }
  .nutrition-meta { position: absolute; left: 138px; top: 308px; color: var(--red); font-weight: 700; font-size: 13px; line-height: 16px; }
  .nutrition-meta span { font-weight: 400; }
  .nutrition-table { position: absolute; left: 112px; top: 350px; }
  .nutrition-table text { font-family: "Arimo", Arial, sans-serif; font-weight: 700; fill: var(--red); font-size: 17px; }
  .produce-art {
    position: absolute; left: 22px; top: 684px; width: 523px; height: 160px;
    background: linear-gradient(90deg, #e9864a 0%, #c9302c 30%, #8a4a3a 50%, #f0a32f 70%, #7a2a4a 90%, #5a9a3a 100%);
    opacity: .55; border-radius: 6px;
  }
  .produce-ground { position: absolute; left: 40px; top: 851px; width: 485px; height: 4px; background: #b5b5b5; border-radius: 2px; }
  .storage-pill {
    position: absolute; left: 170px; top: 878px; width: 243px; height: 43px; border-radius: 12px;
    background: var(--pill); border: 2px solid #1c6f99; color: #0f2c44; font-weight: 700; font-size: 18px;
    display: flex; align-items: center; justify-content: center;
  }
  .allergen { position: absolute; left: 0; width: 556px; top: 926px; text-align: center; color: var(--red); font-weight: 700; font-size: 16px; line-height: 27px; }
  .claims { position: absolute; left: 0; width: 556px; top: 988px; text-align: center; color: var(--ink); font-weight: 700; font-size: 16px; line-height: 24px; }
  .claims .count { margin-right: 22px; }
</style>
</head>
<body>
<div class="label">
  <section class="side-instructions">
    <svg class="backdrop" width="495" height="1050" viewBox="0 0 495 1050" aria-hidden="true">
      <defs>
        <linearGradient id="greyFade" x1="0" y1="0" x2="1" y2="1">
          <stop offset="0" stop-color="#a8a8ab"/>
          <stop offset="1" stop-color="#6f6f72"/>
        </linearGradient>
      </defs>
      <polygon points="170,0 495,0 495,440" fill="url(#greyFade)"/>
      <polygon points="0,760 495,1050 0,1050" fill="url(#greyFade)"/>
      <polygon points="0,560 495,740 495,1050 0,760" fill="#8c8c8f" opacity=".85"/>
    </svg>
    <div class="brand-disc"><span class="brand-name">TOT HARVEST</span></div>
    <h2 class="instructions-title">Instructions :</h2>
    <div class="step step-1"><div class="step-bar"></div><div class="step-number">1</div><p class="step-text">pop out the design<br>number of cubes</p></div>
    <div class="step step-2"><div class="step-bar"></div><div class="step-number">2</div><p class="step-text">Heat in the microwave<br>on high for 1-2 minutes</p></div>
    <div class="step step-3"><div class="step-bar"></div><div class="step-number">3</div><p class="step-text">Stir and allow to cool<br>before serving.</p></div>
  </section>

  <section class="side-product">
    <h1 class="product-name">Sunny Medley</h1>
    <p class="ingredients">pumpkin, beetroot, carrot<br>red capsicum &amp; sweet potato</p>
    <h3 class="nutrition-title">Nutritional Information</h3>
    <p class="nutrition-meta">Servings per package 3<br>Serving size 2 × 50g cubs <span>(100g)</span></p>
    <svg class="nutrition-table" width="410" height="300" viewBox="0 0 410 300">
      <g stroke="#111" stroke-width="4">
        <line x1="0" y1="2" x2="410" y2="2"/>
        <line x1="169" y1="2" x2="169" y2="290"/>
        <line x1="298" y1="2" x2="298" y2="283"/>
        <line x1="0" y1="123" x2="410" y2="123"/>
        <line x1="0" y1="175" x2="410" y2="175"/>
        <line x1="0" y1="226" x2="410" y2="226"/>
      </g>
      <text x="183" y="35">per 50g</text>
      <text x="183" y="58">cube</text>
      <text x="310" y="35">per 100g</text>
      <text x="310" y="59">serving</text>
      <text x="9" y="90">Energy</text>
      <text x="9" y="111">Protein</text>
      <text x="5" y="143">Total fat</text>
      <text x="5" y="166">-Saturated</text>
      <text x="5" y="194">Carbohydrate</text>
      <text x="5" y="216">-Sugars</text>
      <text x="9" y="247">Dietary fibre</text>
      <text x="9" y="268">Sodium</text>
    </svg>
    <div class="produce-art" role="img" aria-label="Illustration of carrot, red capsicum, sweet potato, yellow capsicum and beetroot characters"></div>
    <div class="produce-ground"></div>
    <div class="storage-pill">Store in freezer - 18 c.</div>
    <p class="allergen">Produced on equipment that also processest<br>fish, wheat, and milk products.</p>
    <p class="claims">No added salt, no added suger<br><span class="count">100</span>Australian product, NT made, dietitian created</p>
  </section>
</div>
</body>
</html>
```